Clinic for cellulit and fat removal

Name of clinic :
Lirava
- Body & Health (this has to be written on the site.)
I need CMS for me to be able to make changes myself.
A webpage for woman searching for a solution to remove fat and cellulit.
The owner is a brazilian woman in Denmark, and want her sense of aestetic shines thru the website.
There needs to be a slide show on the landing page showing big sliding pictures, of the clinic and and the treatments.
The Cryolipolysis, is a treatment freezing fat and cellulit, and this treatment will be the Attraction of the clinic.
Needs These pages in a horisontal fasion. (written in Danish)
Lirava
Behandlinger
- Cryolipolysis
- Trimflox
- Lymfemassage
- Korathelix
- Amberline Tide
Produkter
Priser
Kontakt
Clinic
Coded - Design and coding required
5+ page

```html
<!DOCTYPE html>
<html lang="en">
<head>
<meta charset="utf-8">
<title>Lirava – Body &amp; Health</title>
<link href="https://fonts.googleapis.com/css2?family=Raleway:wght@300;400;500;600;700&family=Open+Sans:ital,wght@0,400;0,600;0,700;1,400&display=swap" rel="stylesheet">
<style>
:root{
  --orange:#f7941d;
  --nav:#3b3b3b;
  --ink:#2b2b2b;
  --text:#555;
  --muted:#888;
  --band:#f4f4f4;
  --white:#fff;
}
*{box-sizing:border-box;margin:0;padding:0}
html,body{width:1200px;height:2821px;overflow:hidden}
body{position:relative;background:var(--white);font-family:"Open Sans",sans-serif;color:var(--text)}
.abs{position:absolute}

/* header */
.site-header{left:0;top:0;width:1200px;height:62px;background:var(--nav)}
.brand{left:162px;top:10px;font-family:"Raleway",sans-serif;font-weight:400;font-size:31px;color:var(--orange)}
.main-nav{left:414px;top:23px;display:flex;gap:0;font-family:"Raleway",sans-serif;font-weight:600;font-size:12px;color:var(--white);text-transform:uppercase}
.main-nav span{position:absolute;white-space:nowrap}
.lang{left:865px;top:23px;font-size:11px;color:var(--white);font-family:"Raleway",sans-serif;white-space:nowrap}
.lang b{color:var(--orange);font-weight:500}
.enquire{left:963px;top:17px;width:75px;height:30px;background:var(--orange);color:var(--white);font-family:"Raleway",sans-serif;font-weight:600;font-size:11px;display:flex;align-items:center;justify-content:center}

/* hero */
.hero{left:0;top:62px;width:1200px;height:512px;background:linear-gradient(90deg,#6f6a64 0%,#8d877f 45%,#a8a198 70%,#8f8880 100%)}
.hero-title{left:162px;top:287px;font-family:"Raleway",sans-serif;font-weight:700;font-size:50px;color:var(--white);letter-spacing:1px}
.hero-arrow{top:296px}
.hero-dots{left:576px;top:535px;display:flex;gap:6px}
.hero-dots i{width:9px;height:9px;border-radius:50%;background:var(--white);display:block}
.hero-dots i:first-child{background:transparent;border:1.5px solid var(--white)}

/* welcome */
.video{left:162px;top:623px;width:414px;height:261px;background:linear-gradient(135deg,#d9d6d3,#b9b5b1 55%,#e6e3e0)}
.welcome-title{left:602px;top:612px;font-family:"Raleway",sans-serif;font-weight:400;font-size:28px;color:var(--ink)}
.welcome-text{left:602px;top:661px;width:438px;font-size:11.5px;line-height:18px;color:var(--text)}
.btn{background:var(--orange);color:var(--white);font-family:"Raleway",sans-serif;font-weight:600;font-size:11.5px;display:flex;align-items:center;justify-content:center;text-transform:uppercase}
.read-more{left:602px;top:845px;width:115px;height:39px}

/* treatments */
.band-head{left:0;top:935px;width:1200px;height:128px;background:var(--band);text-align:center}
.section-title{font-family:"Raleway",sans-serif;font-weight:400;font-size:26px;color:var(--ink)}
.band-head .section-title{margin-top:42px}
.band-head p{margin-top:8px;font-size:11.5px;font-style:italic;color:var(--muted)}
.treat-photo{left:0;top:1063px;width:1200px;height:401px;background:linear-gradient(90deg,#b8a59a 0%,#cdbdb2 35%,#d6d1cf 65%,#a8a8b8 100%)}
.treat-caption{left:300px;top:1200px;width:600px;text-align:center;font-family:"Raleway",sans-serif;font-size:23px;line-height:36px;color:var(--white)}
.pointer{left:242px;top:1452px}
.treat-list{left:162px;top:1528px;width:876px;display:flex}
.treat{width:219px;text-align:center;padding:0 16px}
.treat h3{font-family:"Raleway",sans-serif;font-weight:500;font-size:15px;color:var(--orange);text-transform:uppercase;margin-bottom:16px}
.treat p{font-size:11.5px;line-height:20px;color:var(--text)}
.treat-arrow{top:1572px}

/* blog */
.blog{left:0;top:1689px;width:1200px;height:506px;background:var(--band)}
.blog .section-title{position:absolute;left:0;width:1200px;text-align:center;top:52px}
.card{top:1804px;width:276px;height:316px;background:var(--white)}
.card-img{height:141px;background:linear-gradient(135deg,#d8c3b7,#ece5e0 55%,#c9bdb6)}
.card h4{margin:15px 17px 0;font-family:"Open Sans",sans-serif;font-weight:600;font-size:15px;color:var(--ink)}
.card p{margin:13px 17px 0;font-size:11.5px;line-height:20px;color:var(--text)}
.card .meta{position:absolute;left:0;top:267px;width:100%;border-top:1px solid #ececec;padding:14px 17px 0;font-size:10.5px;color:var(--orange)}

/* testimonials */
.testi-title{left:0;top:2242px;width:1200px;text-align:center}
.quote{left:374px;top:2316px;width:560px;font-size:12px;line-height:23px;font-style:italic;color:var(--text);text-align:center}
.testi-name{left:0;top:2434px;width:1200px;text-align:center;font-family:"Raleway",sans-serif;font-weight:700;font-size:13.5px;color:var(--ink)}

/* footer */
.site-footer{left:0;top:2513px;width:1200px;height:308px;background:var(--orange);color:var(--white)}
.fcol{top:2548px}
.fcol h5{font-family:"Raleway",sans-serif;font-weight:700;font-size:12.5px;text-transform:uppercase;margin-bottom:12px}
.fcol p,.fcol li{font-size:10.5px;line-height:21px;list-style:none}
.socials{left:162px;top:2706px;display:flex;gap:16px}
.socials i{width:10px;height:10px;border-radius:50%;background:var(--white);display:block}
.copyright{left:0;top:2778px;width:1200px;text-align:center;font-size:10px}
.copyright span{margin-left:14px}
</style>
</head>
<body>

<header class="abs site-header">
  <div class="abs brand">Lirava</div>
  <nav class="abs main-nav" style="left:0;top:23px;width:1200px">
    <span style="left:414px">Lirava</span>
    <span style="left:493px">Treatments ▾</span>
    <span style="left:602px">Products</span>
    <span style="left:694px">Pricing</span>
    <span style="left:773px">Contact</span>
  </nav>
  <div class="abs lang"><b>English</b> | Danish</div>
  <div class="abs enquire">ENQUIRE</div>
</header>

<section class="abs hero" role="img" aria-label="Slideshow photo of a woman's waist and hips in white underwear"></section>
<h1 class="abs hero-title">BODY &amp; HEALTH</h1>
<svg class="abs hero-arrow" style="left:26px" width="46" height="46" viewBox="0 0 46 46"><circle cx="23" cy="23" r="22" fill="none" stroke="#fff" stroke-opacity=".7" stroke-width="1.5"/><path d="M26 16l-7 7 7 7" fill="none" stroke="#fff" stroke-width="2"/></svg>
<svg class="abs hero-arrow" style="left:1121px" width="46" height="46" viewBox="0 0 46 46"><circle cx="23" cy="23" r="22" fill="none" stroke="#fff" stroke-opacity=".7" stroke-width="1.5"/><path d="M20 16l7 7-7 7" fill="none" stroke="#fff" stroke-width="2"/></svg>
<div class="abs hero-dots"><i></i><i></i><i></i><i></i></div>

<section>
  <div class="abs video" role="img" aria-label="Video still of a cryolipolysis treatment on a client's leg"></div>
  <svg class="abs" style="left:339px;top:722px" width="60" height="60" viewBox="0 0 60 60"><circle cx="30" cy="30" r="28" fill="#2a2a2a" fill-opacity=".85" stroke="#fff" stroke-width="2.5"/><path d="M24 18l18 12-18 12z" fill="#fff"/></svg>
  <h2 class="abs welcome-title">Welcome to Lirava</h2>
  <p class="abs welcome-text">Sed ut perspiciatis unde omnis iste natus error sit voluptatem accusantium doloremque laudantium, totam rem aperiam, eaque ipsa quae ab illo inventore veritatis et quasi architecto beatae vitae dicta sunt explicabo. Nemo enim ipsam voluptatem quia voluptas sit aspernatur aut odit aut fugit, sed quia consequuntur magni dolores eos qui ratione voluptatem sequi nesciunt. Neque porro quisquam est, qui dolorem ipsum quia dolor sit amet, consectetur, adipisci velit, sed quia non numquam eius modi tempora incidunt ut labore et dolore magnam aliquam quaerat. Ut enim ad minima veniam, quis nostrum exercitationem ullam corporis suscipit.</p>
  <div class="abs btn read-more">Read More</div>
</section>

<section>
  <div class="abs band-head">
    <h2 class="section-title">Our Treatments</h2>
    <p>Lorem ipsum dolor sit amet, consectetadipis cing elitsed do eiusm.</p>
  </div>
  <div class="abs treat-photo" role="img" aria-label="Photo of a relaxed client receiving a cryolipolysis treatment from a gloved therapist"></div>
  <p class="abs treat-caption">The Cryolipolysis, is a treatment<br>freezing fat and cellulit, and this treatment<br>will be the Attraction of the clinic.</p>
  <svg class="abs pointer" width="24" height="12" viewBox="0 0 24 12"><path d="M0 12L12 0l12 12z" fill="#fff"/></svg>
  <svg class="abs treat-arrow" style="left:105px" width="12" height="16" viewBox="0 0 12 16"><path d="M8 3L3 8l5 5" fill="none" stroke="#333" stroke-width="2"/></svg>
  <svg class="abs treat-arrow" style="left:1081px" width="12" height="16" viewBox="0 0 12 16"><path d="M4 3l5 5-5 5" fill="none" stroke="#333" stroke-width="2"/></svg>
  <div class="abs treat-list">
    <div class="treat"><h3>Cryolipolysis</h3><p>Lorem ipsum dolor sit ametc sect tadipis cing elit, sed do eiusmod temor incididunt utlor labore et dorea.</p></div>
    <div class="treat"><h3>Trimflox</h3><p>Lorem ipsum dolor sit ametc sect tadipis cing elit, sed do eiusmod temor incididunt utlor labore et dorea.</p></div>
    <div class="treat"><h3>Lymfemassage</h3><p>Lorem ipsum dolor sit ametc sect tadipis cing elit, sed do eiusmod temor incididunt utlor labore et dorea.</p></div>
    <div class="treat"><h3>Korathelix</h3><p>Lorem ipsum dolor sit ametc sect tadipis cing elit, sed do eiusmod temor incididunt utlor labore et dorea.</p></div>
  </div>
</section>

<section class="abs blog">
  <h2 class="section-title">Latest Blog News</h2>
</section>
<article class="abs card" style="left:162px">
  <div class="card-img" role="img" aria-label="Photo of a body contouring device on a client's back"></div>
  <h4>Sed ut perspiciatis unde</h4>
  <p>Lorem ipsum dolor sit amet, consectetadipis cing elit, sed do eiusmod tempor incididunt ut labore et dolore magna aliqua.</p>
  <div class="meta">▣ Apr 06, 2017 &nbsp;✎ Comments</div>
</article>
<article class="abs card" style="left:463px">
  <div class="card-img" role="img" aria-label="Photo of hands pressing the skin of a thigh"></div>
  <h4>Sed ut perspiciatis unde</h4>
  <p>Lorem ipsum dolor sit amet, consectetadipis cing elit, sed do eiusmod tempor incididunt ut labore et dolore magna aliqua.</p>
  <div class="meta">▣ Apr 06, 2017 &nbsp;✎ Comments</div>
</article>
<article class="abs card" style="left:762px">
  <div class="card-img" role="img" aria-label="Photo of a treatment device on a client's abdomen"></div>
  <h4>Sed ut perspiciatis unde</h4>
  <p>Lorem ipsum dolor sit amet, consectetadipis cing elit, sed do eiusmod tempor incididunt ut labore et dolore magna aliqua.</p>
  <div class="meta">▣ Apr 06, 2017 &nbsp;✎ Comments</div>
</article>

<section>
  <h2 class="abs section-title testi-title">Testimonials</h2>
  <svg class="abs" style="left:248px;top:2296px" width="108" height="106" viewBox="0 0 108 106"><circle cx="36" cy="53" r="36" fill="#f7941d"/><text x="20" y="58" font-family="Open Sans" font-size="14" fill="#fff">❝</text></svg>
  <div class="abs" style="left:282px;top:2299px;width:72px;height:72px;border-radius:50%;border:3px solid #fff;background:linear-gradient(160deg,#cfcfcf,#8a8a8a)" role="img" aria-label="Portrait of the client giving the testimonial"></div>
  <p class="abs quote"><b style="font-style:normal;font-size:16px">❝</b> Sed ut perspiciatis unde omnis iste natus error sit voluptatelorem accusan tium doloremque laudantium, totam rem aperiam, eaque ipsa quaeab illo inven tore veritatis et quasi architecto beatae vitae dicta sunt expli caboeo enim ipsam voluptatem quia voluptas sit aspernatur aut odit aut fugit sed quia cons euntur magni dolores eosui rtatem quia voluptas sit aspernatur sit aspernatur aatone. <b style="font-style:normal;font-size:16px">❞</b></p>
  <p class="abs testi-name">Elin Hansen, City Name</p>
</section>

<footer class="abs site-footer"></footer>
<div class="abs fcol" style="left:162px;width:270px">
  <h5>Lirava</h5>
  <p>Lorem ipsum dolor sit amet, consec tortetur adip iscing elit, sed do eiusmod temporikord idunt ut labore et dolore magna aliquaenim ad minim veniam, quis nostrud exercitation ullamco laboris nisi ut aliquip</p>
</div>
<div class="abs socials"><i></i><i></i><i></i><i></i><i></i></div>
<div class="abs fcol" style="left:463px">
  <h5>More Information</h5>
  <ul><li>Wrinkle Injections</li><li>Dermal Fillers</li><li>Lip Enhancements</li><li>Velorin Double Chin Treatment</li><li>Glow Factor Injection</li><li>Growth Factor Injections</li><li>PRP for Hair Loss</li></ul>
</div>
<div class="abs fcol" style="left:698px">
  <h5>Links</h5>
  <ul><li>Fat Reduction vs Weight Loss</li><li>Before &amp; After</li><li>Lose Your Double Chin</li><li>Lirava Reviews</li><li>Am I a Candidate?</li></ul>
</div>
<div class="abs fcol" style="left:909px">
  <h5>Nav</h5>
  <ul><li>Lirava</li><li>Behandlinger</li><li>Produkter</li><li>Priser</li><li>Kontakt</li></ul>
</div>
<p class="abs copyright" style="color:#fff">© 2017 Lirava. Copyright All Rights Reserved.<span>Privacy Policy</span><span>Terms and Conditions</span><span>Find local providers</span></p>

</body>
</html>
```